Business Card for my New Brokerage

Looking to get a business card design for my new Real Estate Brokerage.
I want it with Picture, Phone Number, Email, Website, Office Address
Name and Designation. Please add logo too.

Target Market(s)

Real Estate Investors or Home Buyers

Industry/Entity Type

Real Estate

Contact Information for Business Card

Name, Email, Phone Number, website, email, office address

Colors
EB3D1F
EC4F4E
F09395
F8D3D4
FCEDEE

Requirements
Must have
• Minimalistic, Clean, Modern, Photo
Nice to have
• White and Red Colors

```html
<!DOCTYPE html>
<html lang="en">
<head>
<meta charset="utf-8">
<title>Ember Homes Co – Business Card</title>
<link rel="stylesheet" href="https://fonts.googleapis.com/css2?family=Arimo:wght@400;700&display=swap">
<style>
  :root {
    --canvas-bg: #c4c4c4;
    --brand-red: #dd0000;
    --paper: #ffffff;
    --ink: #111111;
    --gold-dark: #c0913d;
    --gold-light: #f6e39a;
    --edge-gold: #c9a45a;
  }
  * { box-sizing: border-box; margin: 0; padding: 0; }
  html, body { width: 1200px; height: 800px; overflow: hidden; }
  body {
    background: var(--canvas-bg);
    font-family: "Arimo", Arial, sans-serif;
    position: relative;
  }
  .card {
    position: absolute;
    top: 245px;
    width: 540px;
    height: 310px;
    border-radius: 18px;
    border: 2px solid var(--edge-gold);
    overflow: hidden;
    box-shadow: 0 12px 30px rgba(0,0,0,0.25);
  }
  .card--front { left: 40px; background: var(--paper); }
  .card--back { left: 620px; background: var(--brand-red); }

  .front-bands { position: absolute; inset: 0; }

  .holder { position: absolute; left: 36px; top: 34px; }
  .holder__name {
    color: var(--brand-red);
    font-weight: 700;
    font-size: 24px;
    letter-spacing: 0.5px;
  }
  .holder__role {
    color: var(--ink);
    font-size: 14px;
    margin-top: 3px;
  }

  .contacts {
    position: absolute;
    left: 40px;
    top: 122px;
    list-style: none;
    color: var(--paper);
    font-size: 14px;
  }
  .contacts__item {
    display: flex;
    align-items: center;
    gap: 8px;
    height: 23px;
  }
  .contacts__icon { width: 13px; height: 13px; flex: none; }

  .office {
    position: absolute;
    left: 40px;
    top: 236px;
    color: var(--ink);
    font-size: 14px;
    line-height: 20px;
    font-style: normal;
  }

  .brand {
    position: absolute;
    left: 0; right: 0; top: 104px;
    text-align: center;
    color: var(--paper);
    font-weight: 700;
  }
  .brand__name {
    font-size: 62px;
    letter-spacing: 2px;
    line-height: 1;
    display: inline-flex;
    align-items: flex-end;
    gap: 6px;
  }
  .brand__mark {
    width: 9px; height: 9px;
    background: var(--paper);
    margin-bottom: 6px;
  }
  .brand__tagline {
    font-size: 20px;
    letter-spacing: 9px;
    margin-top: 10px;
  }
</style>
</head>
<body>

  <section class="card card--front" aria-label="Card front">
    <svg class="front-bands" width="540" height="310" viewBox="0 0 540 310" aria-hidden="true">
      <defs>
        <linearGradient id="goldSheen" x1="0" y1="0" x2="1" y2="1">
          <stop offset="0" stop-color="#b8862f"/>
          <stop offset="0.5" stop-color="#f6e39a"/>
          <stop offset="1" stop-color="#b8862f"/>
        </linearGradient>
      </defs>
      <polygon points="0,112 320,80 320,176 0,208" fill="var(--brand-red)"/>
      <polygon points="320,80 540,58 540,154 320,176" fill="url(#goldSheen)"/>
    </svg>

    <div class="holder">
      <h1 class="holder__name">DANIEL MERCER</h1>
      <p class="holder__role">Managing Director</p>
    </div>

    <ul class="contacts">
      <li class="contacts__item">
        <svg class="contacts__icon" viewBox="0 0 16 16" aria-hidden="true"><path d="M3.5 1.5l2.5 3-1.5 1.8c.9 2 2.3 3.4 4.2 4.2l1.8-1.5 3 2.5-1.6 2.5C6.5 13.6 2.4 9.5 1 4z" fill="currentColor"/></svg>
        044-555 010 234
      </li>
      <li class="contacts__item">
        <svg class="contacts__icon" viewBox="0 0 16 16" aria-hidden="true"><rect x="1" y="3" width="14" height="10" fill="currentColor"/><path d="M1 3l7 6 7-6" stroke="#dd0000" stroke-width="1.4" fill="none"/></svg>
        hello@emberhomes.co
      </li>
      <li class="contacts__item">
        <svg class="contacts__icon" viewBox="0 0 16 16" aria-hidden="true"><circle cx="8" cy="8" r="6.5" fill="none" stroke="currentColor" stroke-width="1.4"/><ellipse cx="8" cy="8" rx="2.8" ry="6.5" fill="none" stroke="currentColor" stroke-width="1.2"/><path d="M1.5 8h13" stroke="currentColor" stroke-width="1.2"/></svg>
        www.emberhomes.co
      </li>
    </ul>

    <address class="office">
      88, Harbor Lane, Suite 4<br>
      30417, Westland
    </address>
  </section>

  <section class="card card--back" aria-label="Card back">
    <div class="brand">
      <div class="brand__name">EMBER<span class="brand__mark"></span></div>
      <div class="brand__tagline">HOMES CO</div>
    </div>
  </section>

</body>
</html>
```